Bright and beautiful business card for a coach

I'm a personal and business coach based in Perth, Australia. I need a business card that whilst subtle and elegant, will stand out and appeal on a table full of cards.

My business name is Fern Mentoring and the business card must represent the warmth and brightness implied in the name, without being gimmicky. It must have a warmth and appeal and be easy to read.

I prefer clean, minimalist designs.

It must align with the feel of my website and socials: https://www.fernmentoring-example.com.au/
https://www.instagram.com/fernmentoringau/
https://www.facebook.com/fernmentoringau
Updates

Hi Designers Thank you so much for taking the time to submit designs. I wonder if I could have explained myself a little better. Most of the designs that have been submitted look rather formal and many have quite corporate looking embellishments on them (to my eye). I would like softer, warmer, more organic. I’m open to people playing about and being more abstract, using softer embellishments (e.g the line drawing flowers and grasses I’ve used in my socials) incorporating other colours from my palette or like the social icons in my email signature (in PDF), perhaps playing with size/oversize, playing with the bleed. Please don’t be constrained by what I’ve already done, it merely needs to compliment. I’m sorry if I’m not using the right words or have led you astray. I’m no designer, but I’ve done my website, socials, email signature etc all myself (my logo was a design contest) and I was really hoping for my business card to be something more creative than I could have made with a template. Reminder: No black cards/sides please. Thank you 😊

Target Market(s)

Individuals, most likely but not all female. Creative thinkers. Likely professionals.

Industry/Entity Type

Business & Personal Coach

Contact Information for Business Card

(Fern Mentoring Logo) Name: Greta Pellham; Title: Business & Personal Coach; Phone number: +61 (0)458 913307; Email: greta@fernmentoring-example.com.au; Website: https://fernmentoring-example.com.au; Social icons for Facebook, Instagram & LinkedIn: @fernmentoringAU. Optional strapline: "A thinking partner to help you cut through the noise"

Font styles to use
Sans Serif

Colors
00AB8E
00BBA5
67D7C9
C6EFE9
E9F9F6
59FF00
82FF00
B8FF75
E3FFCB
F4FFEA
FFC000
F8CF3A
FAE287
FDF2CF
FEFAEE

Requirements
Must have
• Must align with feel of my website and socials. Must have a pop of #FFC000 (possibly whole of one side, or at least a block). Bright or white background. Easy to read.
Nice to have
• Possibly incorporate the sunshine/grass picture I have used in website and socials - will upload.
Should not have
• Must not be black or dark. Not impersonal or corporate looking.

```html
<!DOCTYPE html>
<html lang="en">
<head>
<meta charset="utf-8">
<title>Fern Mentoring – Business Card</title>
<link rel="stylesheet" href="https://fonts.googleapis.com/css2?family=Poppins:wght@400;500;600&display=swap">
<style>
  :root {
    --canvas: #d9d9db;
    --card-light: #ffffff;
    --card-warm: #FFC000;
    --card-cream: #FEFAEE;
    --gold: #e0951f;
    --gold-bright: #f2ae2c;
    --ink: #2a2a2a;
    --ink-soft: #5a5348;
  }
  * { box-sizing: border-box; margin: 0; padding: 0; }
  html, body {
    width: 1200px; height: 800px; overflow: hidden;
    background: var(--canvas);
    font-family: "Poppins", sans-serif;
  }
  .sheet {
    width: 1200px; height: 800px;
    display: flex; align-items: center; justify-content: center; gap: 40px;
  }
  .card {
    position: relative;
    width: 540px; height: 309px;
    border-radius: 18px;
    overflow: hidden;
    box-shadow: 0 10px 24px rgba(0, 0, 0, 0.12);
  }

  /* Front */
  .card-front { background: var(--card-warm); }
  .card-front .divider { position: absolute; inset: 0; }
  .card-front .brand-name {
    position: absolute; left: 305px; top: 94px;
    font-size: 26px; font-weight: 500; color: var(--ink);
    letter-spacing: 0.5px;
  }
  .contact {
    position: absolute; left: 28px; top: 186px;
    color: var(--ink);
  }
  .contact .person-name {
    font-size: 20px; font-weight: 600; color: var(--gold);
    line-height: 1.15;
  }
  .contact .person-title {
    font-size: 12px; font-weight: 400; margin-bottom: 6px;
  }
  .contact-list { list-style: none; }
  .contact-list li {
    display: flex; align-items: center; gap: 7px;
    font-size: 11.5px; line-height: 18px;
  }
  .contact-list svg { width: 10px; height: 10px; flex: none; }

  /* Back */
  .card-back { background: var(--card-cream); }
  .card-back .brand-name {
    position: absolute; left: 0; right: 0; top: 112px;
    text-align: center;
    font-size: 38px; font-weight: 400; color: var(--ink);
    letter-spacing: 1px;
  }
  .social {
    position: absolute; left: 0; right: 0; top: 222px;
    display: flex; align-items: center; justify-content: center; gap: 5px;
    color: var(--ink-soft); font-size: 13px;
  }
  .social .dot {
    width: 15px; height: 15px; border-radius: 50%;
    background: var(--card-warm);
  }
  .social .handle { margin-left: 4px; }
</style>
</head>
<body>
<main class="sheet">
  <section class="card card-front" aria-label="Card front">
    <svg class="divider" viewBox="0 0 540 309" width="540" height="309" aria-hidden="true">
      <path d="M0,0 L118,0 C70,70 90,175 200,172 C300,168 372,205 350,309 L0,309 Z" fill="var(--card-light)"/>
      <path d="M118,0 C70,70 90,175 200,172 C300,168 372,205 350,309" fill="none" stroke="var(--gold)" stroke-width="5" stroke-linecap="round"/>
    </svg>
    <div class="brand-name">Fern Mentoring</div>
    <div class="contact">
      <p class="person-name">Greta Pellham</p>
      <p class="person-title">Business &amp; Personal Coach</p>
      <ul class="contact-list">
        <li>
          <svg viewBox="0 0 10 10"><path d="M2 0.8 L3.6 0.8 L4.2 3 L3 3.8 C3.6 5.2 4.8 6.4 6.2 7 L7 5.8 L9.2 6.4 L9.2 8 C9.2 8.8 8.6 9.2 7.8 9.2 C4 8.8 1.2 6 0.8 2.2 C0.8 1.4 1.2 0.8 2 0.8 Z" fill="var(--gold)"/></svg>
          +61 (0)458 913307
        </li>
        <li>
          <svg viewBox="0 0 10 10"><rect x="0.5" y="2" width="9" height="6.5" rx="0.8" fill="var(--gold)"/><path d="M0.8 2.4 L5 5.6 L9.2 2.4" fill="none" stroke="#fff" stroke-width="0.9"/></svg>
          greta@fernmentoring-example.com.au
        </li>
        <li>
          <svg viewBox="0 0 10 10"><circle cx="5" cy="5" r="4.5" fill="var(--gold)"/><path d="M0.7 5 H9.3 M5 0.6 C3 3 3 7 5 9.4 M5 0.6 C7 3 7 7 5 9.4" fill="none" stroke="#fff" stroke-width="0.7"/></svg>
          fernmentoring-example.com.au
        </li>
      </ul>
    </div>
  </section>

  <section class="card card-back" aria-label="Card back">
    <div class="brand-name">Fern Mentoring</div>
    <div class="social">
      <span class="dot"></span><span class="dot"></span><span class="dot"></span>
      <span class="handle">@fernmentoringAU</span>
    </div>
  </section>
</main>
</body>
</html>
```